Flat Belly Design Graphics for Social

I want to create 9 social media graphics (new Instagram size 4:5 (1080 x 1350 pixels) focusing on our Flat Belly Graphics, using the pics attached. Use the attached pics, NO RANDOM STOCK PHOTOGRAPHY. For the color scheme of the graphics, the color palette is attached. YOU MUST POST ALL 9 GRAPHICS IN ONE ENTRY.
Using the 3 titles below, create one set of graphics. 1) with all text, then for the others, use the pictures as detailed below in IMPORTANT:
1. Ten-Week Bright Morning Reboot
2. The Quick Garden Kitchen Menu Guide
3. Studio Habits for Lasting Energy Past Midlife - Zero Gym Needed
IMPORTANT:
Only use RK Pic 1 and RK Pic 2 with the title, Ten-Week Bright Morning Reboot
Only use meal plan1 and meal plan2 pics with the title, Quick Garden Kitchen Menu Guide
Only use studio habits 1 and studio habits 2 pics with the title, Studio Habits for Lasting Energy Past Midlife - Zero Gym Needed
women over 40

```html
<!DOCTYPE html>
<html lang="en">
<head>
<meta charset="utf-8">
<title>Social Graphics Set</title>
<link href="https://fonts.googleapis.com/css2?family=Saira+Extra+Condensed:ital,wght@0,700;1,800&family=Oswald:wght@500&display=swap" rel="stylesheet">
<style>
:root{
  --canvas:#ffffff;
  --blush:#f6e3e5;
  --blush-light:#fbeff0;
  --forest:#1f4a3b;
  --rose:#c94f78;
  --rose-soft:#e39bb2;
  --cream:#f7f1e3;
  --gold:#c9a24a;
}
*{margin:0;padding:0;box-sizing:border-box}
html,body{width:1200px;height:3042px;overflow:hidden;background:var(--canvas)}
.board{display:grid;grid-template-columns:repeat(3,1fr);grid-template-rows:repeat(6,1fr);gap:8px;padding:8px;width:1200px;height:3042px}
.tile{position:relative;overflow:hidden;background:radial-gradient(circle at 30% 20%,var(--blush-light),var(--blush) 70%)}
.title{position:absolute;left:8px;right:8px;z-index:2;text-align:center;font-family:"Saira Extra Condensed",sans-serif;font-style:italic;font-weight:800;text-transform:uppercase;line-height:.95;letter-spacing:-.5px;white-space:nowrap}
.title span{display:block}
.title .tag{font-size:.72em;margin-top:2px}
.forest{color:var(--forest)}
.rose{color:var(--rose)}
.rose-soft{color:var(--rose-soft)}
.upright{font-family:"Oswald",sans-serif;font-style:normal;font-weight:500;line-height:1.1;letter-spacing:0}
.photo{position:absolute;z-index:1}
.photo-portrait{background:linear-gradient(180deg,#3a2a26 0%,#8a5a44 30%,#f3efe9 55%,#1b1b1d 80%)}
.photo-meal{background:linear-gradient(135deg,#5a3b2a,#b86a45 40%,#e8e2d6 55%,#7aa04a 80%,#c23a2a)}
.photo-friends{background:linear-gradient(120deg,#3b2a24,#b9886a 45%,#f2ece6 75%,#d9d4cf)}
.photo-friends-light{background:linear-gradient(120deg,#e8d4c6,#c89a7a 45%,#f4ece6 75%,#b8c8d6)}
.art-friends{background:linear-gradient(160deg,var(--forest),var(--rose) 60%,var(--rose-soft))}
svg.deco{position:absolute;left:0;top:0;width:100%;height:100%}
</style>
</head>
<body>
<main class="board">

<section class="tile">
  <h2 class="title" style="top:130px;font-size:58px"><span class="forest">Ten-Week</span><span class="rose">Bright</span><span class="rose">Morning</span><span class="rose">Reboot</span></h2>
</section>

<section class="tile">
  <svg class="deco" viewBox="0 0 389 498"><polygon points="0,498 40,498 190,330 170,320" fill="var(--forest)"/><polygon points="50,498 110,498 270,300 240,290" fill="var(--rose)"/><polygon points="330,150 389,90 389,110 340,160" fill="var(--rose-soft)"/></svg>
  <div class="photo photo-portrait" role="img" aria-label="Smiling woman in a white cropped sweater pointing at her waist" style="right:10px;top:30px;width:160px;height:468px;border-radius:80px 80px 0 0"></div>
  <h2 class="title" style="top:100px;left:16px;right:auto;text-align:left;font-size:36px"><span class="forest">Ten-Week</span><span class="rose-soft">Bright</span><span class="rose-soft">Morning</span><span class="rose">Reboot</span></h2>
</section>

<section class="tile">
  <svg class="deco" viewBox="0 0 389 498"><rect x="330" y="0" width="10" height="55" fill="var(--forest)"/><rect x="346" y="0" width="8" height="75" fill="var(--rose)"/><rect x="48" y="400" width="10" height="98" fill="var(--rose)"/><rect x="66" y="430" width="10" height="68" fill="var(--forest)"/></svg>
  <div class="photo photo-portrait" role="img" aria-label="Smiling woman in a white cropped sweater gesturing to her waist" style="left:100px;top:215px;width:190px;height:283px;border-radius:90px 90px 0 0"></div>
  <h2 class="title" style="top:32px;font-size:44px"><span class="forest">Ten-Week</span><span class="rose-soft">Bright</span><span class="rose-soft">Morning</span><span class="rose-soft">Reboot</span></h2>
</section>

<section class="tile">
  <h2 class="title" style="top:130px;font-size:48px"><span class="forest">The Quick</span><span class="rose-soft">Garden</span><span class="rose-soft">Kitchen</span><span class="rose-soft">Menu Guide</span></h2>
</section>

<section class="tile">
  <svg class="deco" viewBox="0 0 389 498"><polygon points="220,40 270,0 300,0 240,52" fill="var(--rose-soft)"/><polygon points="0,498 30,498 120,420 100,410" fill="var(--forest)"/><polygon points="60,498 100,498 170,440 150,430" fill="var(--rose)"/></svg>
  <h2 class="title" style="top:128px;font-size:44px"><span class="forest">The Quick</span><span class="rose-soft" style="font-size:34px">Garden Kitchen</span></h2>
  <div class="photo photo-meal" role="img" aria-label="Fresh vegetables, fruit and fish framing a meal plan notepad" style="left:42px;top:248px;width:304px;height:212px"></div>
</section>

<section class="tile">
  <svg class="deco" viewBox="0 0 389 498"><polygon points="0,498 40,498 150,400 120,390" fill="var(--forest)"/><polygon points="70,498 110,498 200,420 180,410" fill="var(--rose)"/><polygon points="340,120 389,70 389,100 350,140" fill="var(--rose-soft)"/></svg>
  <h2 class="title" style="top:70px;font-size:50px"><span class="forest">The Quick</span><span class="rose-soft" style="font-size:36px">Garden Kitchen</span></h2>
  <div class="photo photo-meal" role="img" aria-label="Chicken breast, asparagus, berries and grains around a meal plan sheet" style="left:42px;top:225px;width:310px;height:208px;border:3px solid #fff"></div>
</section>

<section class="tile">
  <h2 class="title" style="top:140px;font-size:40px"><span class="forest">Studio Habits</span><span class="rose">For Lasting</span><span class="rose">Energy Past</span><span class="rose">Midlife</span><span class="rose tag">- Zero Gym Needed</span></h2>
</section>

<section class="tile">
  <svg class="deco" viewBox="0 0 389 498"><polygon points="0,80 70,0 110,0 0,120" fill="var(--forest)"/><polygon points="0,50 50,0 60,0 0,60" fill="var(--rose)"/><path d="M0,300 Q200,240 389,260 L389,300 Q200,290 0,330Z" fill="var(--forest)"/><path d="M0,330 Q200,290 389,300 L389,330 Q200,320 0,350Z" fill="var(--rose)"/></svg>
  <h2 class="title" style="top:48px;font-size:34px"><span class="forest">Studio Habits</span><span class="rose">For Lasting</span><span class="rose">Energy Past</span><span class="rose">Midlife</span><span class="rose tag">- Zero Gym Needed</span></h2>
  <div class="photo photo-friends" role="img" aria-label="Two women sharing a surprised whisper" style="left:30px;top:325px;width:340px;height:173px;border-radius:50px 0 0 0"></div>
</section>

<section class="tile">
  <div class="photo photo-friends-light" role="img" aria-label="Two women whispering, one looking surprised" style="left:105px;top:36px;width:180px;height:160px;border-radius:40px"></div>
  <h2 class="title" style="top:212px;font-size:40px"><span class="forest">Studio Habits</span><span class="rose">For Lasting</span><span class="rose">Energy Past</span><span class="rose">Midlife</span><span class="rose tag">- Zero Gym Needed</span></h2>
</section>

<section class="tile">
  <h2 class="title" style="top:180px;font-size:62px"><span class="forest">Extra</span><span class="rose-soft">Graphics</span></h2>
</section>

<section class="tile">
  <svg class="deco" viewBox="0 0 389 498"><path d="M260,0 L389,0 L389,200 Q320,140 300,60Z" fill="var(--rose-soft)" opacity=".6"/><path d="M0,250 Q80,180 180,230 Q120,330 0,340Z" fill="var(--cream)"/><path d="M250,440 Q340,400 389,420 L389,498 L230,498Z" fill="var(--rose-soft)" opacity=".6"/></svg>
  <h2 class="title" style="top:36px;font-size:34px"><span class="forest">Studio Habits</span><span class="rose">For Lasting</span><span class="rose">Energy Past</span><span class="rose">Midlife</span><span class="rose tag">- Zero Gym Needed</span></h2>
  <div class="photo photo-friends" role="img" aria-label="Two women sharing a surprised whisper" style="left:40px;top:245px;width:310px;height:205px;border-radius:45% 55% 40% 60% / 50% 45% 55% 50%"></div>
</section>

<section class="tile">
  <h2 class="title" style="top:126px;font-size:40px"><span class="forest">Studio Habits</span><span class="rose">For Lasting</span><span class="rose">Energy Past</span><span class="rose">Midlife -</span><span class="rose">Zero Gym</span><span class="rose">Needed</span></h2>
</section>

<section class="tile">
  <svg class="deco" viewBox="0 0 389 498"><polygon points="0,470 130,370 150,380 0,498" fill="var(--forest)"/><polygon points="40,498 200,380 230,380 80,498" fill="var(--rose)"/><polygon points="350,120 389,80 389,110 360,135" fill="var(--rose-soft)"/></svg>
  <h2 class="title" style="top:44px;font-size:40px"><span class="forest">The Quick</span><span class="rose-soft">Garden</span><span class="rose-soft">Kitchen</span><span class="rose-soft">Menu Guide</span></h2>
  <div class="photo photo-meal" role="img" aria-label="Chicken breast, asparagus, berries and grains around a meal plan sheet" style="left:75px;top:232px;width:245px;height:158px"></div>
</section>

<section class="tile">
  <svg class="deco" viewBox="0 0 389 498"><polygon points="0,40 60,0 70,0 0,100" fill="var(--forest)"/><polygon points="0,140 40,100 40,120 0,170" fill="var(--rose)"/><polygon points="389,200 260,498 300,498 389,300" fill="var(--forest)"/><polygon points="389,140 200,498 230,498 389,210" fill="var(--rose)"/></svg>
  <h2 class="title" style="top:30px;font-size:34px"><span class="forest">Studio Habits</span><span class="rose">For Lasting</span><span class="rose">Energy Past</span><span class="rose">Midlife</span><span class="rose tag">- Zero Gym Needed</span></h2>
  <div class="photo photo-friends" role="img" aria-label="Two women sharing a surprised whisper" style="left:70px;top:225px;width:250px;height:250px;border-radius:50%;border:4px solid var(--gold)"></div>
</section>

<section class="tile">
  <svg class="deco" viewBox="0 0 389 498"><path d="M40,455 L372,455 L360,410 L50,465Z" fill="var(--rose)"/><path d="M355,250 L380,245 L370,400 Z" fill="var(--forest)"/></svg>
  <h2 class="title" style="top:38px;font-size:34px"><span class="forest">Studio Habits</span><span class="rose">For Lasting</span><span class="rose">Energy Past</span><span class="rose">Midlife</span><span class="rose tag">- Zero Gym Needed</span></h2>
  <div class="photo photo-friends" role="img" aria-label="Two women sharing a surprised whisper" style="left:28px;top:250px;width:340px;height:190px;border-radius:120px 0 120px 0;transform:skewX(-6deg)"></div>
</section>

<section class="tile">
  <h2 class="title upright" style="top:20px;font-size:24px"><span class="forest">Studio Habits</span><span class="rose">For Lasting Energy</span><span class="rose">Past Midlife</span><span class="forest">- Zero Gym Needed</span></h2>
  <svg class="deco" viewBox="0 0 389 498"><path d="M30,360 Q20,230 150,230 Q300,220 330,320 Q360,450 220,470 Q60,490 30,360Z" fill="var(--forest)"/><path d="M20,400 Q40,330 120,340 Q90,440 40,450Z" fill="var(--rose)"/></svg>
  <div class="photo photo-friends-light" role="img" aria-label="Two women whispering, one looking surprised" style="left:80px;top:200px;width:240px;height:280px;border-radius:110px 110px 20px 20px"></div>
</section>

<section class="tile">
  <svg class="deco" viewBox="0 0 389 498"><polygon points="280,60 389,0 389,20 300,70" fill="var(--forest)"/><polygon points="290,90 389,30 389,50 310,100" fill="var(--rose)"/></svg>
  <div class="photo art-friends" role="img" aria-label="Flat illustration of two women whispering a secret" style="left:50px;top:0;width:290px;height:230px;border-radius:0 0 60px 60px"></div>
  <h2 class="title" style="top:248px;font-size:38px"><span class="forest">Studio Habits</span><span class="rose">For Lasting</span><span class="rose">Energy Past</span><span class="rose">Midlife</span><span class="rose tag">- Zero Gym Needed</span></h2>
</section>

<section class="tile">
  <svg class="deco" viewBox="0 0 389 498"><g stroke="var(--forest)" stroke-width="3"><line x1="60" y1="200" x2="110" y2="240"/><line x1="30" y1="300" x2="95" y2="300"/><line x1="330" y1="200" x2="280" y2="240"/><line x1="360" y1="300" x2="295" y2="300"/></g></svg>
  <div class="photo photo-portrait" role="img" aria-label="Smiling woman in a white cropped sweater pointing at her waist" style="left:95px;top:150px;width:200px;height:348px;border-radius:90px 90px 0 0"></div>
  <h2 class="title" style="top:40px;font-size:34px"><span class="rose">Ten-Week</span><span class="rose">Bright Morning</span></h2>
  <h2 class="title" style="top:340px;font-size:44px"><span class="forest">Reboot</span></h2>
</section>

</main>
</body>
</html>
```